Business card design for Brivo Tandem

We need a new business card design along with all the necessary to place an order. The company is Brivo Tandem and we recently updated our logo.

```html
<!DOCTYPE html>
<html lang="en">
<head>
<meta charset="UTF-8">
<title>Brivo Tandem – Business Card</title>
<link href="https://fonts.googleapis.com/css2?family=Montserrat:wght@400;500;700&display=swap" rel="stylesheet">
<style>
  :root {
    --backdrop: #d3d8d8;
    --card-white: #f1f1ef;
    --card-grey: #7b7b7b;
    --accent-yellow: #f0c419;
    --ink-dark: #2e2e2e;
    --logo-tone: #bdbdbd;
  }
  * { margin: 0; padding: 0; box-sizing: border-box; }
  html, body {
    width: 1200px; height: 881px; overflow: hidden;
    background: var(--backdrop);
    font-family: "Montserrat", sans-serif;
  }
  .sheet {
    position: relative; width: 1200px; height: 881px;
    display: flex; align-items: center; justify-content: center; gap: 60px;
  }
  .card {
    width: 500px; height: 286px; position: relative;
    border-bottom: 4px solid var(--accent-yellow);
    box-shadow: 0 12px 30px rgba(0,0,0,0.12);
  }
  .card-front {
    background: var(--card-white);
    display: flex; align-items: center; justify-content: center; gap: 16px;
    padding-top: 20px;
  }
  .card-back {
    background: var(--card-grey);
    display: flex; align-items: center; justify-content: center;
  }
  .identity { text-align: right; white-space: nowrap; align-self: flex-start; margin-top: 122px; }
  .identity-name {
    color: var(--accent-yellow); font-weight: 700; font-size: 19px;
    letter-spacing: 0.5px; text-transform: uppercase; line-height: 24px;
  }
  .identity-role {
    color: var(--ink-dark); font-size: 13px; font-weight: 500; margin-top: 2px;
  }
  .divider {
    width: 2px; height: 60px; background: var(--accent-yellow);
    align-self: flex-start; margin-top: 130px;
  }
  .contact-list { list-style: none; align-self: flex-start; margin-top: 150px; white-space: nowrap; }
  .contact-item {
    display: flex; align-items: center; gap: 8px;
    color: var(--ink-dark); font-size: 12.5px; line-height: 21px;
  }
  .contact-icon { width: 11px; height: 11px; fill: var(--accent-yellow); flex: none; }
  .brand-lockup { display: flex; align-items: center; gap: 16px; }
  .brand-mark { width: 24px; height: 24px; background: var(--logo-tone); }
  .brand-name {
    color: var(--logo-tone); font-weight: 700; font-size: 34px;
    letter-spacing: 3px; text-transform: uppercase;
  }
</style>
</head>
<body>
<main class="sheet">
  <section class="card card-front">
    <div class="identity">
      <p class="identity-name">Daniel Harwood</p>
      <p class="identity-role">Managing Director</p>
    </div>
    <div class="divider"></div>
    <ul class="contact-list">
      <li class="contact-item">
        <svg class="contact-icon" viewBox="0 0 24 24"><path d="M6.6 10.8a15 15 0 0 0 6.6 6.6l2.2-2.2c.3-.3.7-.4 1-.2 1.1.4 2.3.6 3.6.6.6 0 1 .4 1 1V20c0 .6-.4 1-1 1A17 17 0 0 1 3 4c0-.6.4-1 1-1h3.5c.6 0 1 .4 1 1 0 1.3.2 2.5.6 3.6.1.3 0 .7-.2 1z"/></svg>
        555 210 348
      </li>
      <li class="contact-item">
        <svg class="contact-icon" viewBox="0 0 24 24"><path d="M2 5h20v14H2z"/></svg>
        hello@brivotandem.com
      </li>
      <li class="contact-item">
        <svg class="contact-icon" viewBox="0 0 24 24"><circle cx="12" cy="12" r="10"/></svg>
        www.brivotandem.com
      </li>
    </ul>
  </section>
  <section class="card card-back">
    <div class="brand-lockup">
      <span class="brand-mark"></span>
      <span class="brand-name">Brivo Tandem</span>
    </div>
  </section>
</main>
</body>
</html>
```